Business Card for a Dental Office

The design should communicate integrity, quality and reliability. We also want the card look elegant, simple, but still stand out, different from the traditional-dental-office business card.

Industry/Entity Type

Business

```html
<!DOCTYPE html>
<html lang="en">
<head>
<meta charset="utf-8">
<title>Harlow Dental Studio – Business Card</title>
<link rel="stylesheet" href="https://fonts.googleapis.com/css2?family=Open+Sans:wght@400;600;700&display=swap">
<style>
  :root {
    --canvas: #3b3431;
    --card-dark: #111111;
    --card-light: #ffffff;
    --gold: #d9b91c;
    --gold-deep: #a8860f;
    --ink: #1a1a1a;
    --ink-soft: #333333;
    --text-light: #e8e8e8;
  }
  * { box-sizing: border-box; margin: 0; padding: 0; }
  html, body { width: 1200px; height: 900px; overflow: hidden; }
  body {
    background: var(--canvas);
    font-family: "Open Sans", Arial, sans-serif;
    position: relative;
  }
  .card {
    position: absolute;
    top: 300px;
    width: 520px;
    height: 300px;
    border-radius: 4px;
    box-shadow: 0 10px 30px rgba(0,0,0,.45);
  }

  /* Front – dark side */
  .card-front { left: 50px; background: var(--card-dark); color: var(--text-light); }
  .front-brand {
    position: absolute; left: 34px; top: 110px; width: 200px;
    display: flex; align-items: center; gap: 12px;
  }
  .brand-square { width: 30px; height: 30px; background: var(--gold); flex: none; }
  .front-brand .brand-name {
    font-weight: 700; font-size: 21px; line-height: 1.15; color: #ffffff;
  }
  .divider {
    position: absolute; left: 262px; top: 40px; width: 1px; height: 220px;
    background: var(--gold); opacity: .8;
  }
  .contact { position: absolute; left: 284px; top: 52px; font-size: 14px; line-height: 1.35; }
  .contact .person { color: var(--gold); font-weight: 600; font-size: 17px; }
  .contact .role { margin-bottom: 16px; }
  .contact .address { margin-bottom: 14px; }
  .contact-line { display: flex; align-items: center; gap: 10px; }
  .contact-line svg { width: 12px; height: 12px; flex: none; fill: var(--gold); }

  /* Back – appointment side */
  .card-back { left: 630px; background: var(--card-light); color: var(--ink); padding: 30px 34px; }
  .back-brand { display: flex; align-items: center; gap: 12px; margin-left: 30px; }
  .back-brand .brand-square { width: 34px; height: 34px; }
  .back-brand .brand-name { font-weight: 700; font-size: 22px; color: var(--ink); text-transform: uppercase; }
  .tagline {
    margin-left: 76px; margin-top: -2px;
    font-size: 10.5px; font-weight: 700; letter-spacing: .5px; text-transform: uppercase;
    color: var(--gold-deep);
  }
  .appointment-title { margin: 14px 0 14px 40px; font-size: 19px; font-weight: 700; }
  .field { display: flex; align-items: baseline; gap: 6px; font-size: 14px; font-weight: 700; margin-bottom: 14px; }
  .field .label { width: 52px; }
  .dots { flex: 1; border-bottom: 2px dotted var(--ink-soft); transform: translateY(-3px); }
  .notice { font-size: 13.5px; font-weight: 600; color: var(--ink-soft); margin-top: 4px; }
</style>
</head>
<body>

<section class="card card-front" aria-label="Business card front">
  <div class="front-brand">
    <span class="brand-square"></span>
    <span class="brand-name">Harlow Dental Studio</span>
  </div>
  <div class="divider"></div>
  <div class="contact">
    <p class="person">Daniel Marsh</p>
    <p class="role">Managing Director</p>
    <p class="address">12345, Address Goes Here<br>Country Name, 123456.</p>
    <p class="contact-line">
      <svg viewBox="0 0 12 12"><path d="M2.5 0.5 L4.5 0.5 L5.5 3.5 L4 4.6 C4.7 6 6 7.3 7.4 8 L8.5 6.5 L11.5 7.5 L11.5 9.5 C11.5 10.6 10.6 11.5 9.5 11.5 C4.5 11.2 0.8 7.5 0.5 2.5 C0.5 1.4 1.4 0.5 2.5 0.5 Z"/></svg>
      044-555 010 200
    </p>
    <p class="contact-line">
      <svg viewBox="0 0 12 12"><path d="M0.5 2 H11.5 V10 H0.5 Z M1.5 3 L6 6.5 L10.5 3 Z" fill-rule="evenodd"/></svg>
      info@harlowdental.com
    </p>
    <p class="contact-line">
      <svg viewBox="0 0 12 12"><circle cx="6" cy="6" r="5.5"/><path d="M6 0.5 V11.5 M0.5 6 H11.5" stroke="#111" stroke-width="1" fill="none"/></svg>
      www.harlowdental.com
    </p>
  </div>
</section>

<section class="card card-back" aria-label="Appointment card">
  <div class="back-brand">
    <span class="brand-square"></span>
    <span class="brand-name">Harlow Dental Studio</span>
  </div>
  <p class="tagline">Your smile is your gift to others</p>
  <h2 class="appointment-title">Your Next Appointment is</h2>
  <div class="field"><span class="label">Name :</span><span class="dots"></span></div>
  <div class="field"><span class="label">Date :</span><span class="dots"></span></div>
  <div class="field"><span class="label">Time:</span><span class="dots"></span><span>AM</span><span class="dots"></span><span>PM</span></div>
  <p class="notice">If unable to keep appointment, kindly give 24hrs notice.</p>
</section>

</body>
</html>
```